RTavenor Business Cards & Letterhead

I have a logo but need a design for some new business cards. We are a Design-Build Firm that specializes in the design and construction of commercial projects.
the cards need to be professional. no cartoon stuff.
i would like to have the cards in AI format so I can update the card as needed. Logo is provided.
Our Address is: 4187 Marlowe Ct. Apex, North Carolina 27614

```html
<!DOCTYPE html>
<html lang="en">
<head>
<meta charset="utf-8">
<title>RTavenor Business Card</title>
<link href="https://fonts.googleapis.com/css2?family=Open+Sans:wght@400;600;700&display=swap" rel="stylesheet">
<style>
  :root {
    --stage: #e9e7e4;
    --card-dark: #222328;
    --card-black: #0b0b0c;
    --pattern-light: #8a8b8e;
    --brand-blue: #1a6fb5;
    --brand-blue-deep: #124f86;
    --text-light: #f2f3f5;
  }
  * { margin: 0; padding: 0; box-sizing: border-box; }
  html, body { width: 1200px; height: 780px; overflow: hidden; }
  body {
    background: var(--stage);
    font-family: "Open Sans", Arial, sans-serif;
    display: flex;
    align-items: center;
    justify-content: center;
    gap: 60px;
  }
  .card {
    position: relative;
    width: 380px;
    height: 660px;
    border-radius: 26px;
    overflow: hidden;
    box-shadow: 0 14px 30px rgba(0,0,0,0.25);
  }

  /* Back side */
  .card-back { background: var(--card-black); }
  .pattern-field {
    position: absolute;
    inset: 0;
    background:
      linear-gradient(125deg, var(--pattern-light) 0%, #3a3b3e 30%, #16171a 55%, var(--card-black) 100%);
  }
  .back-wordmark {
    position: absolute;
    left: 236px;
    top: 40px;
    height: 330px;
    writing-mode: vertical-rl;
    transform: rotate(180deg);
    display: flex;
    align-items: center;
    gap: 12px;
    font-weight: 700;
    font-size: 40px;
    letter-spacing: 3px;
    color: #9a9ca0;
  }
  .back-wordmark .mark-square {
    width: 26px; height: 26px;
    background: var(--brand-blue);
  }

  /* Front side */
  .card-front { background: var(--card-dark); }
  .front-wordmark {
    position: absolute;
    top: 130px;
    left: 0; right: 0;
    display: flex;
    align-items: center;
    justify-content: center;
    gap: 14px;
    font-weight: 700;
    font-size: 40px;
    letter-spacing: 2px;
    color: var(--brand-blue);
  }
  .front-wordmark .mark-square {
    width: 34px; height: 34px;
    background: var(--brand-blue);
  }
  .contact-block {
    position: absolute;
    left: 44px;
    bottom: 70px;
    color: var(--text-light);
  }
  .person-name {
    font-size: 27px;
    font-weight: 700;
    letter-spacing: 1px;
    color: var(--brand-blue);
    line-height: 1.1;
  }
  .person-title {
    font-size: 17px;
    font-weight: 600;
    margin-bottom: 22px;
  }
  .address { font-size: 15px; line-height: 1.45; margin-bottom: 22px; }
  .contact-list { list-style: none; font-size: 15px; line-height: 1.6; }
  .contact-list li { display: flex; align-items: center; gap: 10px; }
  .contact-list svg { width: 14px; height: 14px; fill: var(--brand-blue-deep); flex: none; }
</style>
</head>
<body>

  <section class="card card-back">
    <div class="pattern-field" role="img" aria-label="Repeating brand pattern in silver fading to black"></div>
    <div class="back-wordmark">
      <span class="mark-square"></span>
      <span>RTAVENOR</span>
    </div>
  </section>

  <section class="card card-front">
    <div class="front-wordmark">
      <span class="mark-square"></span>
      <span>RTAVENOR</span>
    </div>
    <div class="contact-block">
      <h1 class="person-name">ROBERT TAVENOR</h1>
      <p class="person-title">Founder/President</p>
      <p class="address">4187 Marlowe Ct. Apex,<br>North Carolina 27614</p>
      <ul class="contact-list">
        <li>
          <svg viewBox="0 0 24 24" aria-hidden="true"><path d="M6.6 10.8a15 15 0 0 0 6.6 6.6l2.2-2.2a1 1 0 0 1 1-.25 11.4 11.4 0 0 0 3.6.57 1 1 0 0 1 1 1V20a1 1 0 0 1-1 1A17 17 0 0 1 3 4a1 1 0 0 1 1-1h3.5a1 1 0 0 1 1 1c0 1.25.2 2.45.57 3.57a1 1 0 0 1-.25 1z"/></svg>
          (919) 555-0148
        </li>
        <li>
          <svg viewBox="0 0 24 24" aria-hidden="true"><circle cx="12" cy="12" r="10"/></svg>
          www.rtavenor.com
        </li>
        <li>
          <svg viewBox="0 0 24 24" aria-hidden="true"><path d="M2 5h20v14H2z M2 5l10 8 10-8" /></svg>
          RLT@RTavenor.com
        </li>
      </ul>
    </div>
  </section>

</body>
</html>
```